Brightfen Business Card Redesign & Logo Update

We need to update our business cards to something more modern and fresh. Brightfen can provide the current color schemes and old design examples, but welcome creativity in helping us with this redesign. PLEASE NOTE that we no longer utilize the "tree" and/or "leaf" imagery in our branding. If able would apprecaite an update on the quality of our "words only" logo in Ai. / PNG formats too.

Target Market(s)

Investors, landowners, corporate partners, contractors

Industry/Entity Type

Environmental Restoration & Conservation

Contact Information for Business Card

Logo, persons name, title, mailing address, phone and email, website url

Font styles to use
Other font styles liked:
• Merriweather

Requirements
Nice to have
• Logo, persons name, title, mailing address, phone and email, website url, but open to ideams
Should not have
• No all back backgrounds

```html
<!DOCTYPE html>
<html lang="en">
<head>
<meta charset="utf-8">
<title>Brightfen Business Card</title>
<link rel="stylesheet" href="https://fonts.googleapis.com/css2?family=Montserrat:wght@400;500;700;800&display=swap">
<style>
  :root {
    --brand-green: #167a3f;
    --brand-orange: #f07f1e;
    --ink: #2a2a2a;
    --paper: #ffffff;
    --backdrop: #2b2b2b;
  }
  * { margin: 0; padding: 0; box-sizing: border-box; }
  html, body { width: 1200px; height: 900px; overflow: hidden; }
  body {
    background: var(--backdrop);
    font-family: "Montserrat", sans-serif;
    position: relative;
  }
  .card {
    position: absolute;
    left: 280px;
    width: 640px;
    height: 366px;
    border-radius: 22px;
    overflow: hidden;
  }
  .card--front { top: 60px; background: var(--paper); }
  .card--back { top: 474px; background: var(--brand-green); }

  .wordmark {
    position: absolute;
    font-weight: 800;
    letter-spacing: 1px;
    line-height: 1;
  }
  .tagline {
    position: absolute;
    font-weight: 700;
    letter-spacing: 1.6px;
    text-transform: uppercase;
  }
  .card--front .wordmark { left: 44px; top: 42px; font-size: 50px; color: var(--brand-green); }
  .card--front .tagline { left: 46px; top: 98px; font-size: 9.5px; color: var(--brand-green); }

  .divider {
    position: absolute;
    left: 40px; right: 40px; top: 214px;
    height: 1px;
    background: var(--brand-green);
  }
  .holder {
    position: absolute;
    right: 40px; top: 150px;
    text-align: right;
  }
  .holder__name { font-size: 24px; font-weight: 800; letter-spacing: 1px; }
  .holder__first { color: var(--brand-green); }
  .holder__last { color: var(--brand-orange); }
  .holder__title { font-size: 15px; font-weight: 500; color: var(--ink); margin-top: 2px; }

  .contact-list {
    position: absolute;
    left: 40px; top: 228px;
    list-style: none;
    font-size: 14px;
    color: var(--ink);
  }
  .contact-list li { display: flex; align-items: center; gap: 8px; height: 24px; }
  .contact-list svg { width: 13px; height: 13px; fill: var(--brand-orange); flex: none; }

  .address {
    position: absolute;
    right: 40px; top: 232px;
    text-align: right;
    font-size: 14px;
    line-height: 22px;
    color: var(--ink);
  }
  .edge-band { position: absolute; left: 0; bottom: 0; width: 640px; height: 14px; }

  .card--back .brand-lockup {
    position: absolute; inset: 0;
    display: flex; flex-direction: column; align-items: center; justify-content: center;
    color: var(--paper);
  }
  .card--back .wordmark { position: static; font-size: 64px; }
  .card--back .tagline { position: static; font-size: 12px; margin-top: 10px; letter-spacing: 2.4px; }
</style>
</head>
<body>

<section class="card card--front" aria-label="Business card front">
  <div class="wordmark">BRIGHTFEN</div>
  <div class="tagline">Environmental Credit Company</div>

  <div class="holder">
    <div class="holder__name"><span class="holder__first">DANA</span> <span class="holder__last">MERCER</span></div>
    <div class="holder__title">CEO/Founder</div>
  </div>

  <div class="divider"></div>

  <ul class="contact-list">
    <li>
      <svg viewBox="0 0 24 24" aria-hidden="true"><path d="M6.6 10.8a15.1 15.1 0 0 0 6.6 6.6l2.2-2.2a1 1 0 0 1 1-.25 11.4 11.4 0 0 0 3.6.57 1 1 0 0 1 1 1V20a1 1 0 0 1-1 1A17 17 0 0 1 3 4a1 1 0 0 1 1-1h3.5a1 1 0 0 1 1 1c0 1.25.2 2.45.57 3.57a1 1 0 0 1-.25 1z"/></svg>
      (555) 014 2280
    </li>
    <li>
      <svg viewBox="0 0 24 24" aria-hidden="true"><path d="M2 5h20v14H2z M2 5l10 8 10-8" fill="var(--brand-orange)"/><path d="M2.5 5.5l9.5 7.5 9.5-7.5" fill="none" stroke="#fff" stroke-width="1.6"/></svg>
      Dana@brightfen.com
    </li>
    <li>
      <svg viewBox="0 0 24 24" aria-hidden="true"><circle cx="12" cy="12" r="10"/><path d="M2 12h20M12 2c3 3 3 17 0 20M12 2c-3 3-3 17 0 20" fill="none" stroke="#fff" stroke-width="1.4"/></svg>
      www.brightfen.com
    </li>
  </ul>

  <div class="address">
    48 Alder Crossing Road<br>
    Fenwick Vale, AB 60318
  </div>

  <svg class="edge-band" viewBox="0 0 640 14" preserveAspectRatio="none" aria-hidden="true">
    <polygon points="0,0 320,0 334,14 0,14" fill="var(--brand-orange)"/>
    <polygon points="328,0 640,0 640,14 342,14" fill="var(--brand-green)"/>
  </svg>
</section>

<section class="card card--back" aria-label="Business card back">
  <div class="brand-lockup">
    <div class="wordmark">BRIGHTFEN</div>
    <div class="tagline">Environmental Credit Company</div>
  </div>
</section>

</body>
</html>
```